'Little Lantern' promotional brochure

We have designed a 6 week program to educate impending first-time parents about the things they need to know to survive the first 6 months. Sessions delivered by general practitioner/family doctor, dietician, physiotherapist, speech pathologist and psychologist. Our promotional blurb is: 'A comprehensive education program for first-time parents-to-be, delivered over 6 weeks by health professionals in your community, about everything you need to know to look after your baby (and yourself!) in the first 6 months'. I now want to put together a promotional brochure to be distributed to those couples who express an interest which will provide further details of what will be delivered in the course.
Updates
In terms of layout, I envisaged a double sided A4 size, foldable into 3 sections, but very happy to be guided on this.
Target Market(s)
To appeal to a young, well educated demographic. First time parents couples.
Industry/Entity Type
Medical
Font styles to use
Other font styles liked:
- Playfair Display
Requirements
Must have
- Playfair display font to be consistent with our logo (attached). Logo also included please. Some consistency with colours of logo please.
Nice to have
- I am a doctor, and have no creative genes! But prefer a clean and professional appearance overall. Not too cluttered in overall appearance.
Should not have
- No cheesy pictures of babies.

```html
<!DOCTYPE html>
<html lang="en">
<head>
<meta charset="utf-8">
<title>Little Lantern – Brochure</title>
<link href="https://fonts.googleapis.com/css2?family=Playfair+Display:wght@400;700;900&display=swap" rel="stylesheet">
<style>
:root{
  --green:#8dc63f;
  --green-deep:#5bb131;
  --green-text:#4fa82e;
  --white:#ffffff;
  --paper:#fbfbfb;
  --bg:#e9e9e9;
  --photo-warm-a:#e9ddd4;
  --photo-warm-b:#c9b7a8;
}
*{box-sizing:border-box;margin:0;padding:0}
html,body{width:1200px;height:1000px;overflow:hidden}
body{background:var(--bg);font-family:'Playfair Display',Georgia,serif;position:relative}
.sheet{position:absolute;display:flex;box-shadow:0 6px 18px rgba(0,0,0,.18)}
.sheet--outside{left:276px;top:12px;width:666px;height:490px}
.sheet--inside{left:276px;top:522px;width:646px;height:466px}
.panel{position:relative;flex:1;overflow:hidden;background:var(--paper)}
.photo{position:absolute;left:0;right:0;top:0}
.photo--sitting{height:365px;background:linear-gradient(160deg,#7b6a4e,#cfc4b8 55%,#efeae4)}
.photo--hug{height:365px;background:linear-gradient(150deg,#f2ece8 30%,#c99e88 60%,#eee4dc)}
.stripes{position:absolute;left:0;right:0}
.stripes span{display:block;height:4px;background:var(--green);margin-bottom:5px}
.cover-heading{position:absolute;left:0;right:0;text-align:center;color:var(--green-text);font-weight:700;text-transform:uppercase}
/* brand name */
.brand{display:flex;align-items:center;gap:8px;color:var(--green-deep);font-weight:400;text-transform:uppercase;line-height:1.05}
.brand__mark{width:26px;height:26px;background:var(--green-deep);flex:none}
.brand--centre{position:absolute;top:42px;left:0;right:0;justify-content:center;font-size:11px}
.brand--corner{position:absolute;top:24px;right:12px;font-size:9px}
.brand--corner .brand__mark{width:20px;height:20px}
/* middle outside panel */
.intro{position:absolute;left:0;right:0;top:115px;bottom:0;background:var(--green);color:var(--white);text-align:center}
.intro__lines{position:absolute;left:0;right:0}
.intro__lines span{display:block;height:3px;background:var(--white);margin-bottom:5px}
.intro__blurb{position:absolute;top:32px;left:20px;right:20px;font-size:14.2px;line-height:1.33}
.intro__cta{position:absolute;top:236px;left:10px;right:10px;font-weight:700;text-transform:uppercase}
.intro__cta h2{font-size:17px;line-height:1.2}
.intro__cta p{font-size:12px;line-height:1.35;margin-top:4px}
.intro__cta .phone{font-size:15px;margin-top:4px}
/* cover */
.price{position:absolute;top:218px;left:18px;background:var(--green-deep);color:var(--white);text-align:center;padding:4px 10px 3px;font-weight:700;text-transform:uppercase;font-size:10px;line-height:1.15}
.price strong{display:block;font-size:15px}
.title{position:absolute;top:256px;left:20px;right:8px;color:var(--green-deep);font-weight:900;text-transform:uppercase;font-size:38px;line-height:.98;text-align:center}
.cover-months{font-size:19px;line-height:1.05}
.cover-months b{font-size:36px;vertical-align:-4px;margin-right:3px}
/* inside */
.photo--small{height:118px}
.photo--lying{background:linear-gradient(120deg,#f4f2f0,#bdb6b4 55%,#6d5a66)}
.photo--twins{background:linear-gradient(120deg,#4b3226,#b66f4a 45%,#e7c57a 70%,#4a3326)}
.photo--hat{background:linear-gradient(120deg,#dfe6ea,#7cc4c9 40%,#e7c6b3 65%,#c9d8c8)}
.body{position:absolute;top:118px;left:0;right:0;bottom:0;background:var(--green);color:var(--white);padding:0 12px}
.week{font-weight:700;font-size:15px;text-decoration:underline;text-decoration-thickness:1px;text-underline-offset:2px;margin:9px 0 4px}
.week--right{text-align:right}
.body p,.body li{font-size:7.6px;line-height:1.3}
.body p{margin-bottom:7px}
.body b{font-weight:700}
.body ul{list-style:none;margin:0 0 8px 2px}
.body ul li::before{content:". "}
.summary{position:absolute;left:12px;right:12px;bottom:22px;border-top:3px solid var(--white);padding-top:8px}
.summary__box{margin:0 auto;width:112px;background:var(--white);color:var(--green-deep);text-align:center;font-weight:700;text-transform:uppercase;font-size:8.6px;line-height:1.12;padding:8px 6px}
.summary__box b{font-size:17px;display:block;line-height:1}
</style>
</head>
<body>

<section class="sheet sheet--outside">
  <div class="panel">
    <div class="photo photo--sitting" role="img" aria-label="Photo of a baby in a white lace dress and bonnet sitting up"></div>
    <div class="stripes" style="top:353px"><span style="width:100%"></span><span style="width:80%"></span><span style="width:55%"></span></div>
    <h2 class="cover-heading" style="top:398px;font-size:19px;line-height:1.1">How to take<br>best care of<br>your child?</h2>
  </div>

  <div class="panel">
    <div class="brand brand--centre"><span class="brand__mark"></span><span>Wattlebrook<br>Health &amp;<br>Medical</span></div>
    <div class="intro">
      <div class="intro__lines" style="top:14px"><span></span><span style="width:75%;margin-left:auto"></span></div>
      <p class="intro__blurb">A comprehensive education program for first-time parents-to-be, delivered over 6 weeks by health professionals in your community, about everything you need to know to look after your baby (and yourself!) in the first 6 months</p>
      <div class="intro__cta">
        <h2>Join us whoever you are.</h2>
        <p>Contact details for enquiries/bookings<br>--------------</p>
        <p class="phone">(02) 5550 0142</p>
      </div>
      <div class="intro__lines" style="top:355px"><span style="width:70%"></span><span style="width:100%"></span></div>
    </div>
  </div>

  <div class="panel">
    <div class="photo photo--hug" role="img" aria-label="Photo of a mother kissing her smiling baby on the cheek"></div>
    <div class="brand brand--corner"><span class="brand__mark"></span><span>Wattlebrook<br>Health &amp;<br>Medical</span></div>
    <div class="price">Total cost<strong>$300</strong></div>
    <h1 class="title">Little<br>Lantern</h1>
    <div class="stripes" style="top:353px"><span style="width:100%"></span><span style="width:80%;margin-left:auto"></span><span style="width:55%;margin-left:auto"></span></div>
    <h2 class="cover-heading cover-months" style="top:396px">Best baby<br>care for<br><b>6</b>first months</h2>
  </div>
</section>

<section class="sheet sheet--inside">
  <div class="panel">
    <div class="photo photo--small photo--lying" role="img" aria-label="Photo of a baby in a knitted bonnet lying on a blanket"></div>
    <div class="body">
      <div class="stripes" style="top:6px;left:0;right:0"><span style="width:100%;background:var(--white)"></span><span style="width:70%;background:var(--white)"></span></div>
      <h3 class="week week--right" style="margin-top:28px">WEEK 1</h3>
      <p>GP Dr Helena Marsh will share information for Mum's own health after delivery. Topics include:</p>
      <ul>
        <li>Vaccinations in pregnancy</li>
        <li>Bleeding, bladder and bowel after delivery</li>
        <li>Breastfeeding, engorgement and mastitis</li>
        <li>Bottle feeding</li>
        <li>Post-natal anxiety &amp; depression</li>
        <li>Intimacy and contraception</li>
      </ul>
      <h3 class="week">WEEK 2</h3>
      <p>Session 1 - Clinical Psychologist Dr Anya Corbett will discuss changes in relationships as couples become parents, gender roles in parenting and post-natal depression.</p>
      <p>Session 2 - Physiotherapist Tess Harlow will present advice for Mums regarding exercise during and after pregnancy, looking after the pelvic floor during and after pregnancy, and abdominal muscle separation management. She will also provide advice for promoting babies' neck strength and minimising the risk of flat spots on the head and encouraging gross motor skills in the first 6 months</p>
    </div>
  </div>

  <div class="panel">
    <div class="photo photo--small photo--twins" role="img" aria-label="Photo of two laughing babies in red and yellow beanies"></div>
    <div class="body">
      <h3 class="week">WEEK 3</h3>
      <p>Session 1 - Dietician Mia Garland provides advice for Mums regarding healthy eating during pregnancy and lactation, normal weight gain during pregnancy and realistic weight loss after. She will also discuss the evidence regarding <b>breastfeeding VS bottle-feeding</b>, normal infant weight gain and introducing solids (including those with potential for allergy).</p>
      <p>Session 2 - Paediatric Speech Pathologist Ruth Ellery will share information about latching and breast-feeding troubles &amp; tongue tie, advice about dummies and finger-sucking, introducing solids &amp; feeding (including 'pouch' food), encouraging language development and current evidence about electronic devices impacting language development.</p>
      <h3 class="week">WEEK 4</h3>
      <p>GP Dr Helena Marsh will share advice about your babies' health in the first 6 months, including:</p>
      <ul>
        <li>Skin of newborns</li>
        <li>Sleeping</li>
        <li>Crying</li>
        <li>Immunisations</li>
        <li>Fever and infections</li>
        <li>Diarrhoea and constipation</li>
        <li>Teething</li>
        <li>Understanding a baby's signals</li>
      </ul>
    </div>
  </div>

  <div class="panel">
    <div class="photo photo--small photo--hat" role="img" aria-label="Photo of a smiling baby in a teal knitted hat with a red bow"></div>
    <div class="body">
      <h3 class="week" style="margin-top:14px">WEEK 5</h3>
      <p>Clinical Psychologist Dr Anya Corbett will share information about bonding &amp; attachment with your baby, how to promote their social &amp; emotional development and how to manage separation anxiety. She will also discuss positive parenting approaches.</p>
      <h3 class="week">WEEK 6</h3>
      <p>Session 1 - Secret Men's Business - a men-only session (including beer!) with a new father for frank discussion about the road ahead. Mums will do a shopping excursion with the GP &amp; Dietician to Greenmart to look at baby products and food - the good and the bad!</p>
      <p>Session 2 - Program review, reflection and evaluation and future session planning when baby is 6 months of age.</p>
      <div class="summary">
        <div class="summary__box"><b>6</b>weeks of comprehensive parent education program for baby health care for the first 6 months</div>
      </div>
    </div>
  </div>
</section>

</body>
</html>
```